Dalvick's Business Card

I need some designs for a new business card including the new logo attached. An old example of our business card is also attached to show all the data that should be included on the new design.
**I added some more examples someone had mocked up**

Contact Information for Business Card

Should include all info on other examples uploaded.

```html
<!DOCTYPE html>
<html lang="en">
<head>
<meta charset="utf-8">
<title>Dalvick's Business Card</title>
<link href="https://fonts.googleapis.com/css2?family=Montserrat:wght@400;500;600;700&display=swap" rel="stylesheet">
<style>
  :root {
    --page-bg: #e9e6e1;
    --card-white: #ffffff;
    --card-dark: #1d1d1d;
    --brand-blue: #1a6fb8;
    --brand-red: #e2232a;
    --ink: #222222;
    --band-text: #ffffff;
  }
  * { margin: 0; padding: 0; box-sizing: border-box; }
  html, body {
    width: 900px; height: 1200px; overflow: hidden;
    background: var(--page-bg);
    font-family: "Montserrat", Arial, sans-serif;
  }
  .canvas { position: relative; width: 900px; height: 1200px; }

  .card {
    position: absolute; left: 80px; width: 742px; height: 440px;
    border-radius: 28px; overflow: hidden;
    box-shadow: 0 6px 14px rgba(0,0,0,0.35);
  }
  .card-front { top: 132px; background: var(--card-white); }
  .card-back { top: 638px; background: var(--card-dark); }

  .brand-name {
    position: absolute; color: var(--brand-blue);
    font-weight: 700; letter-spacing: 1px; white-space: nowrap;
  }
  .brand-line {
    position: absolute; color: var(--brand-red);
    font-weight: 600; white-space: nowrap;
  }
  .card-front .brand-name { left: 70px; top: 220px; font-size: 44px; }
  .card-front .brand-line { left: 72px; top: 272px; font-size: 12.6px; }

  .divider {
    position: absolute; left: 393px; top: 180px; width: 2px; height: 104px;
    background: var(--brand-blue);
  }
  .contact { position: absolute; left: 426px; top: 186px; }
  .contact-name { color: var(--brand-blue); font-size: 26px; font-weight: 700; margin-bottom: 18px; }
  .contact-row { display: flex; align-items: center; gap: 10px; font-size: 16.5px; color: var(--ink); height: 24px; }
  .contact-row svg { width: 16px; height: 16px; flex: none; }

  .bands { position: absolute; left: 0; bottom: 0; width: 742px; height: 40px; }
  .band-label {
    position: absolute; top: 0; height: 40px; line-height: 40px;
    color: var(--band-text); font-size: 16px; font-weight: 500; letter-spacing: 0.3px;
  }
  .band-left { left: 79px; }
  .band-right { left: 462px; }

  .card-back .brand-name { left: 218px; top: 180px; font-size: 62px; }
  .card-back .brand-line { left: 220px; top: 253px; font-size: 19px; }
  .back-strip { position: absolute; left: 0; bottom: 0; width: 742px; height: 8px; background: var(--brand-red); }
</style>
</head>
<body>
<main class="canvas">
  <section class="card card-front">
    <div class="brand-name">DALVICK'S</div>
    <div class="brand-line">AIR CONDITIONING &amp; HEATING SERVICE</div>

    <div class="divider"></div>

    <div class="contact">
      <div class="contact-name">Mark Dalvick</div>
      <div class="contact-row">
        <svg viewBox="0 0 16 16" aria-hidden="true">
          <path d="M2 6 Q8 1 14 6 L12.5 7.5 L10.5 6 L10.5 5 Q8 4 5.5 5 L5.5 6 L3.5 7.5 Z" fill="#e2232a"/>
          <rect x="4" y="8" width="8" height="6" rx="1" fill="#e2232a"/>
        </svg>
        <span>555.014.2286</span>
      </div>
      <div class="contact-row">
        <svg viewBox="0 0 16 16" aria-hidden="true">
          <rect x="1" y="4" width="14" height="9" fill="#1a6fb8"/>
          <path d="M1 4 L8 9.5 L15 4" fill="none" stroke="#ffffff" stroke-width="1.3"/>
        </svg>
        <span>hvacdalvick@mailbox.com</span>
      </div>
    </div>

    <svg class="bands" viewBox="0 0 742 40" aria-hidden="true">
      <polygon points="0,0 392,0 372,40 0,40" fill="#1a6fb8"/>
      <polygon points="400,0 742,0 742,40 380,40" fill="#e2232a"/>
    </svg>
    <div class="band-label band-left">FAMILY OWNED &amp; OPERATED</div>
    <div class="band-label band-right">LICENSED &amp; INSURED</div>
  </section>

  <section class="card card-back">
    <div class="brand-name">DALVICK'S</div>
    <div class="brand-line">AIR CONDITIONING &amp; HEATING SERVICE</div>
    <div class="back-strip"></div>
  </section>
</main>
</body>
</html>
```